New Business Card Design Project LORVANTI-Italy

we are LORVANTI-Italy
our company in the market for 3 years we are luxury cosmetic company and its about time for a facelift :)
i will like to have elegant luxurious and unique business card
that will give the person that get it a unique, luxurious and elegant impression
I'm VERY OPEN FOR NEW IDEAS , even duo i add a few files of things that i see on line and i like them

i add my logo as well
my website is LORVANTI.COM
(if you would like to see the main style that we have)

Target Market(s)

adult that have money :)

Industry/Entity Type

Business

Contact Information for Business Card

Name - Dario Lorvanti
Position - CEO and CO Founder
address - 4817 E Halvern
telephone - 555-384-1926
email - dario@lorvanti.com
fax - 555-384-1926
website - LORVANTI.COM

Colors
000000
959595
fbee3e
ffffff

Requirements
Must have
• big logo in GOLD color
• elegant look
• impressive
Nice to have
• not must but maybe classy pattern background
• not must but maybe emblem
• maybe clear plastic business card
Should not have
• colors
• images

```html
<!DOCTYPE html>
<html lang="en">
<head>
<meta charset="utf-8">
<title>LORVANTI Italy – Business Card</title>
<link rel="stylesheet" href="https://fonts.googleapis.com/css2?family=Cinzel:wght@500&family=Roboto:wght@400&display=swap">
<style>
  :root {
    --backdrop: #2b2624;
    --card: #111111;
    --card-edge: #1c1c1c;
    --gold: #d6a928;
    --white: #f2f2f2;
    --grey: #959595;
  }
  * { margin: 0; padding: 0; box-sizing: border-box; }
  html, body { width: 1200px; height: 716px; overflow: hidden; }
  body {
    background: var(--backdrop);
    display: flex;
    align-items: center;
    justify-content: center;
    gap: 40px;
  }
  .card {
    width: 520px;
    height: 297px;
    background: var(--card);
    border: 1px solid var(--card-edge);
    border-radius: 4px;
    box-shadow: 0 18px 40px rgba(0,0,0,0.45);
    position: relative;
  }
  .brand {
    display: flex;
    flex-direction: column;
    align-items: center;
    gap: 18px;
  }
  .brand-circle {
    width: 62px;
    height: 62px;
    border-radius: 50%;
    border: 3px solid var(--gold);
  }
  .brand-name {
    font-family: "Cinzel", serif;
    font-weight: 500;
    color: var(--gold);
    letter-spacing: 1px;
  }
  .card-front {
    display: flex;
    align-items: center;
    justify-content: center;
  }
  .card-front .brand-name { font-size: 42px; }
  .card-back {
    display: grid;
    grid-template-columns: 248px 1px 1fr;
    align-items: center;
  }
  .card-back .brand-circle { width: 52px; height: 52px; }
  .card-back .brand-name { font-size: 32px; }
  .divider {
    width: 1px;
    height: 170px;
    background: var(--gold);
  }
  .contact {
    padding-left: 26px;
    font-family: "Roboto", sans-serif;
    color: var(--white);
  }
  .person-name {
    font-family: "Cinzel", serif;
    font-weight: 500;
    font-size: 22px;
    color: var(--gold);
    letter-spacing: 1px;
  }
  .person-role {
    font-size: 13px;
    margin-bottom: 20px;
  }
  .contact-list {
    list-style: none;
    font-size: 13px;
    line-height: 1.7;
  }
</style>
</head>
<body>
  <section class="card card-front">
    <div class="brand">
      <div class="brand-circle"></div>
      <div class="brand-name">LORVANTI</div>
    </div>
  </section>

  <section class="card card-back">
    <div class="brand">
      <div class="brand-circle"></div>
      <div class="brand-name">LORVANTI</div>
    </div>
    <div class="divider"></div>
    <div class="contact">
      <div class="person-name">DARIO LORVANTI</div>
      <div class="person-role">CEO and CO Founder</div>
      <ul class="contact-list">
        <li>Tel. 555-384-1926</li>
        <li>Fax. 555-384-1926</li>
        <li>dario@lorvanti.com</li>
        <li>www.lorvanti.com</li>
        <li>Address. 4817 E Halvern</li>
      </ul>
    </div>
  </section>
</body>
</html>
```